KRT Engineering Business Card Design

We’re looking for an elegant, clean, and timeless business card design that communicates experience, capability, and reliability.

KRT Engineering was established in 1995 , we are a Government Contracting company providing Professional Services to the Office of Frontier Affairs, Harbor Protection and the Vantage Collective. Our capabilities include: Acquisition & Program Management; Intelligence & Security Operations; Cyber, IT & Network Operations; Lifecycle Logistics & Asset Readiness; C5ISR Systems Engineering & Sustainment.

We want the card to reflect a straightforward, confident approach to business. The design should feel polished and professional without being flashy or overly corporate.

Design Direction
Clean, sophisticated, and uncluttered
Elegant but understated
Strong typography and thoughtful spacing
A timeless aesthetic rather than something overly trendy
Confident and established, with a sense of substance
Easy to read and practical in a real-world business setting

The overall impression should be: “These are experienced professionals who know what they’re doing, do what they say, and can be relied upon.”

We’re open to creative interpretations. The finished card should feel distinctive through its typography, proportions, layout, and attention to detail rather than through excessive graphics or visual effects.

We’re looking for a design that would make a potential client immediately feel that they’re dealing with a capable, trustworthy, and established company.

Company Colors: Navy and Gold/Yellow (but you do not need to use these colors on the card)
Company Name: KRT Engineering Associates, Inc. (known as KRT Engineering)
Website: krtengineering.com
Company Logo: Navy & Gold (other variations attached)

```html
<!DOCTYPE html>
<html lang="en">
<head>
<meta charset="utf-8">
<title>KRT Engineering – Business Card</title>
<link rel="stylesheet" href="https://fonts.googleapis.com/css2?family=Plus+Jakarta+Sans:wght@500;600;700;800&family=Barlow:wght@500&display=swap">
<style>
  :root {
    --navy: #1c2552;
    --gold: #c9a23a;
    --gold-line: #b8923a;
    --paper: #efefef;
    --muted: #6e7499;
    --backdrop: #d3d3d3;
    --white: #ffffff;
  }
  * { margin: 0; padding: 0; box-sizing: border-box; }
  html, body { width: 1200px; height: 1200px; overflow: hidden; background: var(--backdrop); }
  body { position: relative; font-family: "Plus Jakarta Sans", sans-serif; color: var(--navy); }

  .card { position: absolute; left: 180px; width: 840px; height: 480px; overflow: hidden; }
  .card--front { top: 78px; background: var(--paper); }
  .card--back { top: 630px; background: var(--navy); }

  /* Front: brand panel */
  .brand-panel { position: absolute; left: 0; top: 0; width: 377px; height: 480px; background: var(--navy); }
  .wordmark { position: absolute; display: flex; align-items: center; gap: 14px; font-weight: 800; letter-spacing: 2px; }
  .wordmark__dot { border-radius: 50%; background: var(--gold); }
  .brand-panel .wordmark { left: 68px; top: 106px; font-size: 84px; color: var(--white); }
  .brand-panel .wordmark__dot { width: 26px; height: 26px; }
  .company-name { position: absolute; font-weight: 600; font-size: 14px; letter-spacing: 5.4px; line-height: 20px; color: var(--muted); text-transform: uppercase; }
  .brand-panel .company-name { left: 68px; top: 274px; }
  .established { position: absolute; left: 68px; top: 378px; font-size: 16px; font-weight: 600; letter-spacing: 1.6px; line-height: 20px; color: var(--muted); }
  .established .year { color: var(--gold); }
  .front-rule { position: absolute; left: 196px; top: 388px; width: 582px; height: 1px; background: var(--gold-line); }

  /* Front: contact */
  .contact { position: absolute; left: 430px; top: 0; width: 350px; }
  .person-name { position: absolute; top: 76px; font-size: 37px; font-weight: 800; white-space: nowrap; letter-spacing: -0.3px; }
  .person-title { position: absolute; top: 126px; font-size: 19px; font-weight: 600; color: var(--gold); white-space: nowrap; }
  .contact-rule { position: absolute; top: 163px; width: 348px; height: 1px; background: var(--gold-line); }
  .contact-row { position: absolute; left: 0; display: flex; gap: 12px; font-size: 21px; font-weight: 500; line-height: 26px; color: #1a1d2e; white-space: nowrap; }
  .contact-row svg { width: 24px; height: 24px; flex: none; margin-top: 1px; }
  .contact-row--phone { top: 191px; }
  .contact-row--address { top: 235px; }
  .contact-row--web { top: 331px; }
  .tagline { position: absolute; top: 398px; font-size: 15px; font-weight: 700; letter-spacing: 1.9px; color: var(--navy); white-space: nowrap; }

  /* Back */
  .back-band { position: absolute; left: 0; top: 0; width: 840px; height: 122px; background: var(--paper); }
  .back-band .wordmark { left: 60px; top: 36px; font-size: 44px; color: var(--navy); gap: 10px; }
  .back-band .wordmark__dot { width: 16px; height: 16px; }
  .back-band .company-name { left: 253px; top: 46px; }
  .back-band .established { left: auto; right: 56px; top: 57px; font-size: 17px; letter-spacing: 1.4px; }

  .services-heading { position: absolute; left: 0; width: 840px; top: 154px; text-align: center; font-size: 22px; font-weight: 700; letter-spacing: 1.6px; color: var(--gold); }
  .sector-rule { position: absolute; left: 55px; width: 731px; height: 1px; }
  .sector-rule--top { top: 192px; background: var(--gold-line); }
  .sector-rule--bottom { top: 236px; background: #5a6288; }
  .sectors { position: absolute; left: 0; width: 840px; top: 201px; text-align: center; font-size: 20px; font-weight: 500; letter-spacing: 1.3px; color: var(--white); white-space: nowrap; }
  .sectors .bullet { display: inline-block; width: 8px; height: 8px; border-radius: 50%; background: var(--gold); vertical-align: middle; margin: 0 8px 4px; }

  .capability { position: absolute; top: 274px; width: 150px; margin-left: -75px; text-align: center; }
  .capability__icon { width: 72px; height: 72px; margin: 0 auto; border-radius: 10px; background: linear-gradient(160deg, #3a4170, #2b3362); border: 1px solid rgba(201,162,58,0.5); }
  .capability__label { margin-top: 26px; font-family: "Barlow", sans-serif; font-weight: 500; font-size: 16px; line-height: 19px; color: var(--white); text-transform: uppercase; }
  .capability__rule { width: 96px; height: 1px; margin: 10px auto 0; background: #8a8fb0; }
</style>
</head>
<body>

<section class="card card--front">
  <div class="brand-panel">
    <div class="wordmark"><span>KRT</span><span class="wordmark__dot"></span></div>
    <p class="company-name">KRT Engineering<br>Associates, Inc.</p>
    <p class="established">ESTABLISHED<br><span class="year">IN 1995</span></p>
  </div>
  <div class="front-rule"></div>

  <div class="contact">
    <h1 class="person-name">Marlene Ardwick</h1>
    <p class="person-title">President, CEO &amp; Founder</p>
    <div class="contact-rule"></div>

    <p class="contact-row contact-row--phone">
      <svg viewBox="0 0 24 24" fill="none" stroke="#c9a23a" stroke-width="1.6" stroke-linejoin="round"><path d="M6 3l3 4-2 2c1 2.5 3.5 5 6 6l2-2 4 3-2 3c-6 0-13-7-13-13z"/><path d="M14 4a6 6 0 0 1 6 6M14 7.5a3 3 0 0 1 3 3"/></svg>
      <span>555-014-2730</span>
    </p>
    <p class="contact-row contact-row--address">
      <svg viewBox="0 0 24 24" fill="none" stroke="#c9a23a" stroke-width="1.4"><path d="M3 21h18M5 21V5l8-2v18M13 9h6v12M8 8h2M8 11h2M8 14h2M8 17h2M16 13h1M16 16h1"/></svg>
      <span>4180 Harrow Lane,<br>Suite 310, Bayport Heights,<br>VA 20145</span>
    </p>
    <p class="contact-row contact-row--web">
      <svg viewBox="0 0 24 24" fill="none" stroke="#c9a23a" stroke-width="1.3"><circle cx="12" cy="12" r="9"/><ellipse cx="12" cy="12" rx="4" ry="9"/><path d="M3 12h18M4.5 7.5h15M4.5 16.5h15"/></svg>
      <span>krtengineering.com</span>
    </p>
    <p class="tagline">EXPERIENCE. CAPABILITY. RELIABILITY.</p>
  </div>
</section>

<section class="card card--back">
  <header class="back-band">
    <div class="wordmark"><span>KRT</span><span class="wordmark__dot"></span></div>
    <p class="company-name">KRT Engineering<br>Associates, Inc.</p>
    <p class="established">ESTABLISHED <span class="year">IN 1995</span></p>
  </header>

  <h2 class="services-heading">PROFESSIONAL SERVICES FOR</h2>
  <div class="sector-rule sector-rule--top"></div>
  <p class="sectors">FRONTIER AFFAIRS<span class="bullet"></span>HARBOR PROTECTION<span class="bullet"></span>VANTAGE COLLECTIVE</p>
  <div class="sector-rule sector-rule--bottom"></div>

  <div class="capability" style="left:104px">
    <div class="capability__icon" role="img" aria-label="Line icon of a handshake over a team"></div>
    <p class="capability__label">Acquisition &amp;<br>Program<br>Management</p>
    <div class="capability__rule"></div>
  </div>
  <div class="capability" style="left:254px">
    <div class="capability__icon" role="img" aria-label="Line icon of a shield with a padlock"></div>
    <p class="capability__label">Intelligence<br>&amp; Security<br>Operations</p>
    <div class="capability__rule"></div>
  </div>
  <div class="capability" style="left:405px">
    <div class="capability__icon" role="img" aria-label="Line icon of a monitor with a cloud network"></div>
    <p class="capability__label">Cyber, IT &amp;<br>Network<br>Operations</p>
    <div class="capability__rule"></div>
  </div>
  <div class="capability" style="left:562px">
    <div class="capability__icon" role="img" aria-label="Line icon of a globe and delivery truck"></div>
    <p class="capability__label">Lifecycle<br>Logistics &amp; Asset<br>Readiness</p>
    <div class="capability__rule"></div>
  </div>
  <div class="capability" style="left:727px">
    <div class="capability__icon" role="img" aria-label="Line icon of a satellite dish"></div>
    <p class="capability__label">C5ISR Systems<br>Engineering &amp;<br>Sustainment</p>
    <div class="capability__rule"></div>
  </div>
</section>

</body>
</html>
```